Anzeigengestaltung für eine Stellenanzeige
Zielgruppe
Stellenanzeige
Wir sind eine Druckerei. Wir suchen für unsere Druckerei einen Buchhalter/in oder bzw. auch für das Rechnungswesen.
Aufgabenstellung
Wir möchten eine Stellenanzeige mit klarer und schneller Wirkung , keine Fließtextanzeige und einer unnötigen Beschreibung wie toll unserer Druckerei ausgestattet ist. Die Anzeige darf bunt und lustig sein Wortspiele wie Zahlenbändiger o.ä. sind erlaubt. Die Stelle soll für 30 bis 40 Stunden Wochenarbeitsstunden ausgeschrieben sein.
Mehr möchten wir gar nicht sagen wir sind ja nicht die kreativsten :-)
Unsere Hausfarbe sind HKS 38 und HKS 6

```html
<!DOCTYPE html>
<html lang="de">
<head>
<meta charset="utf-8">
<title>Stellenanzeige Buchhaltung</title>
<link href="https://fonts.googleapis.com/css2?family=Inter:wght@300;400;700&display=swap" rel="stylesheet">
<style>
  :root {
    --brand-orange: #d9801f;
    --ink: #1a1a1a;
    --paper: #ffffff;
    --asphalt-dark: #5d6166;
    --asphalt-light: #8f9499;
    --panel: rgba(236, 238, 240, 0.88);
  }
  * { margin: 0; padding: 0; box-sizing: border-box; }
  html, body {
    width: 1200px; height: 848px; overflow: hidden;
    background: var(--paper);
    font-family: "Inter", Arial, sans-serif;
    color: var(--ink);
  }
  .ad { position: relative; width: 1200px; height: 848px; background: var(--paper); }

  .hero {
    position: absolute; left: 0; top: 0;
    width: 1146px; height: 658px;
    border-right: 9px solid var(--brand-orange);
    border-bottom: 9px solid var(--brand-orange);
    border-bottom-right-radius: 32px;
    overflow: hidden;
  }
  .hero-photo {
    position: absolute; inset: 0;
    background:
      radial-gradient(ellipse at 82% 40%, rgba(214,120,150,0.35), transparent 45%),
      radial-gradient(ellipse at 30% 30%, rgba(170,190,210,0.35), transparent 55%),
      linear-gradient(135deg, var(--asphalt-light), var(--asphalt-dark));
  }

  .headline {
    position: absolute; left: 58px; top: 76px;
    font-weight: 700; font-size: 72px; line-height: 82px;
    letter-spacing: -0.5px; color: #fff;
    text-shadow: 2px 3px 6px rgba(0,0,0,0.45);
  }

  .offer {
    position: absolute; left: 0; top: 385px;
    width: 814px; height: 202px;
    background: var(--panel);
    border: 2px solid var(--brand-orange); border-left: none;
    border-radius: 0 30px 30px 0;
  }
  .offer p {
    position: absolute; left: 56px; top: 32px;
    font-weight: 300; font-size: 39px; line-height: 45px;
    color: var(--ink);
  }

  .contact {
    position: absolute; top: 700px;
    font-size: 18.5px; line-height: 27px; font-weight: 400;
    font-style: normal;
  }
  .contact-address { left: 56px; }
  .contact-address strong { font-weight: 700; }
  .contact-lines { left: 307px; top: 702px; }

  .brand-name {
    position: absolute; right: 54px; top: 708px;
    font-weight: 700; font-size: 32px;
    color: var(--ink);
  }
</style>
</head>
<body>
  <main class="ad">
    <section class="hero">
      <div class="hero-photo" role="img" aria-label="Foto: Kind hüpft in einem bunten Kleid über Kreide-Hüpfkästchen mit Zahlen auf grauem Asphalt"></div>
      <h1 class="headline">Zahlen bewegen<br>Sie heute immer<br>noch?</h1>
      <div class="offer">
        <p>Dann sind Sie richtig bei uns, denn wir<br>suchen eine/einen Buchhalter/in mit<br>Hang zum Rechnungswesen.</p>
      </div>
    </section>

    <address class="contact contact-address">
      <strong>Kontakt:</strong><br>
      Kranz &amp; Weidel GmbH<br>
      Lindenhofweg 7<br>
      49074 Osnabrück
    </address>
    <div class="contact contact-lines">
      Telefon: +49 (0) 5401 4730-0<br>
      Telefax: +49 (0) 5401 4730-29<br>
      info@kranzundweidel.de
    </div>

    <div class="brand-name">Kranz &amp; Weidel</div>
  </main>
</body>
</html>
```